Indy Film Production Company/Studio

We need a business card designed from an existing logo. We are a digital studio/production company that caters to creating genre entertainment, like Action, Horror, and martial arts. The card along with the logo will be used to Brand the company from letter heads to banners. The design will also be used for postcards and Brochures. It should be professional and masculine.
Updates

Thank you to all the designers who have participated. I'm narrowing down who it will be. Thank you again.

Target Market(s)

Investors, Networks, Producers, and actors

Industry/Entity Type

Film Production

Contact Information for Business Card

Teodoro Valbuena
Producer/Writer/Director
www.kestrelpicturehouse.example

Requirements
Must have
• Website address, Facebook icon and Twitter icon possibly in the back of the card.
Nice to have
• Logline of Company: Follow The Action.

```html
<!DOCTYPE html>
<html lang="en">
<head>
<meta charset="utf-8">
<title>Kestrel Picture House – Business Card</title>
<link rel="stylesheet" href="https://fonts.googleapis.com/css2?family=Roboto:ital,wght@0,400;0,700;1,900&display=swap">
<style>
  :root {
    --backdrop: #a7a4a4;
    --card: #f4f4f4;
    --brand-red: #d3312a;
    --band-red: #c4302b;
    --ink: #1b1b1b;
    --band-dark: #2a2222;
    --white: #ffffff;
  }
  * { margin: 0; padding: 0; box-sizing: border-box; }
  html, body { width: 1200px; height: 1200px; overflow: hidden; }
  body {
    background: var(--backdrop);
    font-family: "Roboto", Arial, sans-serif;
    position: relative;
  }
  .card {
    position: absolute;
    width: 712px;
    height: 419px;
    background: var(--card);
    overflow: hidden;
  }
  .card--front { left: 238px; top: 118px; }
  .card--back  { left: 230px; top: 643px; }

  .brand {
    position: absolute;
    display: flex;
    align-items: center;
    gap: 10px;
    color: var(--brand-red);
    font-weight: 700;
    text-transform: uppercase;
    letter-spacing: 0.5px;
    line-height: 1;
    white-space: nowrap;
  }
  .brand__mark {
    width: 16px; height: 16px;
    background: var(--brand-red);
    flex: none;
  }
  .card--front .brand {
    left: 0; right: 0; top: 196px;
    justify-content: center;
    font-size: 28px;
  }
  .card--back .brand {
    right: 70px; top: 160px;
    font-size: 18px;
  }
  .card--back .brand .brand__mark { width: 12px; height: 12px; }

  .person { position: absolute; left: 40px; top: 80px; }
  .person__name {
    font-weight: 900;
    font-style: italic;
    font-size: 27px;
    color: var(--ink);
  }
  .person__role {
    margin-top: 8px;
    font-size: 16px;
    color: var(--ink);
  }

  .contact {
    position: absolute;
    left: 40px; top: 216px;
    list-style: none;
    font-size: 18px;
    color: var(--ink);
  }
  .contact__item {
    display: flex; align-items: center; gap: 16px;
    height: 29px;
  }
  .contact__icon { width: 18px; height: 14px; fill: var(--brand-red); }

  .address {
    position: absolute;
    left: 40px; top: 283px;
    font-size: 18px;
    line-height: 29px;
    color: var(--ink);
  }

  .footer-band { position: absolute; left: 0; bottom: 0; width: 712px; height: 80px; }
  .footer-links {
    position: absolute;
    right: 40px; bottom: 20px;
    display: flex; align-items: center; gap: 10px;
  }
  .social-dot {
    width: 16px; height: 16px;
    border-radius: 50%;
    background: var(--white);
  }
  .website {
    margin-left: 4px;
    font-size: 17px;
    color: var(--white);
  }
</style>
</head>
<body>

  <section class="card card--front" aria-label="Card front">
    <div class="brand"><span class="brand__mark"></span>Kestrel Picture House</div>
  </section>

  <section class="card card--back" aria-label="Card back">
    <div class="person">
      <h1 class="person__name">Teodoro Valbuena</h1>
      <p class="person__role">Producer/Writer/Director</p>
    </div>

    <div class="brand"><span class="brand__mark"></span>Kestrel Picture House</div>

    <ul class="contact">
      <li class="contact__item">
        <svg class="contact__icon" viewBox="0 0 18 14" aria-hidden="true">
          <path d="M1 5 C1 1 17 1 17 5 L13 5 L13 3.5 C11 2.8 7 2.8 5 3.5 L5 5 Z"/>
          <path d="M5 6 L13 6 L15 13 L3 13 Z"/>
        </svg>
        <span>+00 111 222 3333</span>
      </li>
      <li class="contact__item">
        <svg class="contact__icon" viewBox="0 0 18 14" aria-hidden="true">
          <path d="M1 2 L17 2 L9 8 Z"/>
          <path d="M1 3.5 L9 9.5 L17 3.5 L17 12 L1 12 Z"/>
        </svg>
        <span>teodoro@kestrelpicturehouse.example</span>
      </li>
    </ul>

    <p class="address">Your Long Commercial or<br>business address in 2 line</p>

    <svg class="footer-band" viewBox="0 0 712 80" preserveAspectRatio="none" aria-hidden="true">
      <path d="M0 64 C170 22 430 4 712 10 L712 80 L0 80 Z" fill="var(--band-dark)"/>
      <path d="M110 80 C260 32 470 16 712 18 L712 80 Z" fill="var(--band-red)"/>
    </svg>
    <div class="footer-links">
      <span class="social-dot" role="img" aria-label="Social profile"></span>
      <span class="social-dot" role="img" aria-label="Social profile"></span>
      <span class="website">www.kestrelpicturehouse.example</span>
    </div>
  </section>

</body>
</html>
```